Graphics for New Online Software

Looking at a designer to design a UI/UX Interface for an Online Events Platform (just JPEG) and some corresponding images for a website content (i.e. features etc)

Deliverables:
1x User Interface Design for the Platform (refer to attachment)
5-6x Feature Listing Images (refer to attachment)

Target Market(s)

Technology, Online Users Etc

Industry/Entity Type

Software Developer

Number of Pages Required

1 page

Font styles to use
Sans Serif

Colors
34a7d8
0493ce
3176b5
85acd3

Requirements
Must have
• Looks like a well built software - examples:
https://gravelmoor.io/
https://quintaro.com/

All the images should look very professional, as though you are using it on the online platform itself.
Nice to have
• Refer to attached "Feature Listing" and Logo

```html
<!DOCTYPE html>
<html lang="en">
<head>
<meta charset="utf-8">
<title>Venueloop – Event Platform Screens</title>
<link href="https://fonts.googleapis.com/css2?family=Montserrat:wght@400;500;600;700;800&display=swap" rel="stylesheet">
<style>
:root{
  --page:#dce7f3;
  --white:#ffffff;
  --sidebar:#1380c4;
  --active:#2763a8;
  --heading:#2a5ea8;
  --accent-light:#85acd3;
  --ink:#1b1f3b;
  --muted:#4a4f63;
  --card:#e6f1fd;
  --line:#c9d3df;
  --photo-a:#c9ced6;
  --photo-b:#e9ebee;
  --online:#0493ce;
}
*{box-sizing:border-box;margin:0;padding:0}
html,body{width:746px;height:1200px;overflow:hidden}
body{background:var(--page);font-family:'Montserrat',sans-serif;color:var(--ink);position:relative}
.screen{position:absolute;left:74.5px;width:597px;background:var(--white);box-shadow:0 4px 14px rgba(40,80,130,.08);overflow:hidden}
.screen--event{top:31px;height:393px}
.screen--stage{top:465px;height:393px}
.screen--breakouts{top:892px;height:277px}
.abs{position:absolute}
.brand{position:absolute;top:12px;font-size:11px;font-weight:800;letter-spacing:-.2px;color:var(--ink)}
.search{position:absolute;top:12px;width:165px;height:19px;border:1px solid #e0e4ea;font-size:5.5px;color:#333;padding:0 8px;display:flex;align-items:center;justify-content:space-between}
.duration{position:absolute;right:25px;top:15px;font-size:7.5px;color:#333;display:flex;align-items:center;gap:4px}
.duration b{font-weight:700;color:var(--ink)}
.header-rule{position:absolute;left:95px;right:25px;top:39.5px;border-top:1px solid var(--line)}
.sidebar{position:absolute;left:0;top:39.5px;bottom:0;width:95px;background:var(--sidebar)}
.nav{position:absolute;top:19px;left:0;right:0;list-style:none}
.nav li{height:22.4px;display:flex;align-items:center;padding-left:23px;font-size:6px;font-weight:500;color:var(--white);letter-spacing:.2px;position:relative}
.nav li.is-active{background:var(--active)}
.nav li.is-active::after{content:"";position:absolute;right:-3px;top:8px;border-left:3px solid var(--active);border-top:3px solid transparent;border-bottom:3px solid transparent}
.nav li.is-active svg{position:absolute;right:11px}
.copyright{position:absolute;left:17px;bottom:11px;font-size:4.5px;color:var(--white)}
.section-title{position:absolute;font-size:13px;font-weight:700;color:var(--heading);letter-spacing:.3px}
.section-title::after{content:"";position:absolute;left:0;top:19px;width:22px;height:1.5px;background:linear-gradient(90deg,var(--heading) 0 6px,transparent 6px 8px,var(--heading) 8px 14px,transparent 14px 16px,var(--accent-light) 16px 22px)}
.photo{position:absolute;background:linear-gradient(135deg,var(--photo-b),var(--photo-a))}
.frame{position:absolute;border:1px solid var(--heading)}
.corner-tr{position:absolute;width:19px;height:6px;border-top:2px solid var(--heading);border-right:2px solid var(--heading)}
.corner-bl{position:absolute;width:19px;height:18px;border-bottom:2px solid var(--heading);border-left:2px solid var(--heading)}
.avatar{position:absolute;border-radius:50%;background:radial-gradient(circle at 50% 40%,#d8b7a0,#8a6a58 70%,#5e5450)}
.prog-card{position:absolute;top:88px;width:122px;height:145px;background:var(--card);border-bottom:1.5px solid var(--accent-light);padding:11px 12px}
.prog-card h3{font-size:7px;font-weight:700;line-height:8.5px;color:var(--ink);text-transform:uppercase;padding-bottom:4px;border-bottom:1px solid #b9c7d8;height:39px}
.prog-card .meta{font-size:4px;margin-top:5px;color:var(--muted)}
.prog-card .meta i{margin-right:3px}
.prog-card p{font-size:5.4px;line-height:9px;color:#333;margin-top:2px}
.prog-card .speaker{position:absolute;left:10px;top:105px;width:32px;height:32px}
.prog-card .speaker-name{position:absolute;left:46px;top:111px;font-size:7.5px;font-weight:600}
.prog-card .speaker-role{position:absolute;left:46px;top:123px;font-size:5.2px;color:#333}
.speaker-tile{position:absolute;top:285px;width:66px;text-align:center}
.speaker-tile .avatar{position:static;display:block;width:66px;height:66px}
.speaker-tile span{display:block;margin-top:5px;font-size:9px;font-weight:700}
.play{position:absolute;width:19px;height:19px;border-radius:50%;background:var(--active)}
.play::after{content:"";position:absolute;left:7.5px;top:5.5px;border-left:5px solid #fff;border-top:4px solid transparent;border-bottom:4px solid transparent}
.session{position:absolute;top:270px;width:102px;height:89px;border:1px solid var(--accent-light);background:var(--card)}
.session .photo{position:static;width:100%;height:56px;background:linear-gradient(135deg,#b9c2cd,#6e7784)}
.session small{display:block;font-size:4px;font-weight:600;color:var(--muted);margin:6px 6px 0}
.session strong{display:block;font-size:6px;font-weight:600;color:var(--heading);margin:3px 6px 0}
.chat{position:absolute;left:452.4px;top:39.5px;width:119.4px;bottom:0;background:var(--card)}
.chat-head{height:24.7px;background:var(--sidebar);color:#fff;font-size:7.5px;font-weight:600;display:flex;align-items:center;justify-content:space-between;padding:0 10px}
.chat-head em{font-style:normal;font-weight:800;font-size:6px;color:#cfe6ff}
.chat-item{position:absolute;left:0;right:0;height:44px;border-bottom:1px solid #fff}
.chat-item .avatar{left:19.5px;top:6px;width:32.5px;height:32.5px}
.chat-item b{position:absolute;left:55px;top:10px;font-size:7.5px;font-weight:600}
.chat-item span{position:absolute;left:55px;top:21px;font-size:5.2px;color:#333}
.chat-item .status{top:29px;font-size:3.8px;font-weight:600;display:flex;align-items:center;gap:2px}
.chat-item .status::before{content:"";width:3px;height:3px;border-radius:50%;background:var(--online)}
.room{position:absolute;width:141.6px;height:68px;color:#fff;padding:0 10px}
.room--dark{background:var(--active)}
.room--light{background:var(--sidebar)}
.room h4{position:absolute;left:10px;top:16px;font-size:6.3px;font-weight:700;letter-spacing:.1px}
.room .count{position:absolute;right:8px;top:11px;font-size:12px;font-weight:700}
.room .time{position:absolute;left:10px;top:29px;font-size:5.7px}
.room a{position:absolute;left:10px;top:46px;font-size:4.6px;font-weight:600;color:#fff;text-decoration:underline}
</style>
</head>
<body>

<!-- Event info screen -->
<section class="screen screen--event">
  <div class="brand" style="left:15px">VENUELOOP</div>
  <div class="search" style="left:104px">Search
    <svg width="6" height="6" viewBox="0 0 10 10"><circle cx="4" cy="4" r="3" fill="none" stroke="#333" stroke-width="1"/><path d="M6.3 6.3 9 9" stroke="#333"/></svg></div>
  <div class="duration"><svg width="8" height="8" viewBox="0 0 10 10"><circle cx="5" cy="5" r="4" fill="none" stroke="#333"/><path d="M5 2.5V5l2 1" stroke="#333" fill="none"/></svg>EVENT DURATION : <b>2:00 HRS</b></div>
  <div class="header-rule"></div>
  <aside class="sidebar">
    <ul class="nav">
      <li class="is-active">EVENT INFO <svg width="6" height="6" viewBox="0 0 10 10"><rect x="1" y="2" width="8" height="7" fill="none" stroke="#fff" stroke-width="1.4"/><path d="M3 1v2M7 1v2" stroke="#fff"/></svg></li>
      <li>STAGE</li><li>BREAKOUTS</li><li>BOOTHS</li><li>VIRTUAL EXHIBITION</li><li>REWARDS</li>
    </ul>
    <div class="copyright">© 2020 www.venueloop.com</div>
  </aside>

  <h2 class="section-title" style="left:117px;top:62px">AGENDA</h2>
  <div class="photo" role="img" aria-label="Speaker at a podium with microphones" style="left:117px;top:88px;width:181px;height:124px"></div>
  <div class="frame" style="left:117px;top:88px;width:181px;height:124px"></div>
  <div class="corner-tr" style="left:280px;top:87px;height:18px"></div>
  <div class="corner-bl" style="left:115.5px;top:196px"></div>
  <div class="abs" style="left:253px;top:203px;font-size:7.5px;font-weight:600">-Liana</div>
  <div class="abs" style="left:116px;top:222px;font-size:9.5px;font-weight:600">The Biggest Conference</div>
  <div class="abs" style="left:245px;top:237px;font-size:5.4px;color:#333">The Speaker</div>

  <h2 class="section-title" style="left:321px;top:63px">PROGRAMMING</h2>
  <article class="prog-card" style="left:322px">
    <h3>Vivamus habitant cursus adipiscing senectus.</h3>
    <div class="meta"><i>Duration</i>2:00 hrs</div>
    <p>Lorem ipsum dolor sit amet, has ad habeo tation deterruisset. An eam harum nonumy dolorum, sale dicat commodo mea ad. Sed cu legere ornatus aliquando.</p>
    <div class="avatar speaker" role="img" aria-label="Portrait of speaker Daicy"></div>
    <div class="speaker-name">-Daicy</div><div class="speaker-role">The Speaker</div>
  </article>
  <article class="prog-card" style="left:449.5px">
    <h3>Primis arcu hendrerit purus senectus aenean morbi</h3>
    <div class="meta"><i>Duration</i>2:00 hrs</div>
    <p>Lorem ipsum dolor sit amet, has ad habeo tation deterruisset. An eam harum nonumy dolorum, sale dicat commodo mea ad. Sed cu legere ornatus aliquando.</p>
    <div class="avatar speaker" role="img" aria-label="Portrait of speaker Merry"></div>
    <div class="speaker-name">-Merry</div><div class="speaker-role">The Speaker</div>
  </article>

  <h2 class="section-title" style="left:115.5px;top:252px">SPEAKERS</h2>
  <div class="speaker-tile" style="left:115px"><i class="avatar" role="img" aria-label="Portrait of Linda"></i><span>LINDA</span></div>
  <div class="speaker-tile" style="left:210px"><i class="avatar" role="img" aria-label="Portrait of David"></i><span>DAVID</span></div>
  <div class="speaker-tile" style="left:304.5px"><i class="avatar" role="img" aria-label="Portrait of Droid"></i><span>DROID</span></div>
  <div class="speaker-tile" style="left:399px"><i class="avatar" role="img" aria-label="Portrait of James"></i><span>JAMES</span></div>
  <div class="speaker-tile" style="left:493.5px"><i class="avatar" role="img" aria-label="Portrait of Jhon"></i><span>JHON</span></div>
</section>

<!-- Stage screen -->
<section class="screen screen--stage">
  <div class="brand" style="left:18px">VENUELOOP</div>
  <div class="search" style="left:110px">Search
    <svg width="6" height="6" viewBox="0 0 10 10"><circle cx="4" cy="4" r="3" fill="none" stroke="#333"/><path d="M6.3 6.3 9 9" stroke="#333"/></svg></div>
  <div class="duration"><svg width="8" height="8" viewBox="0 0 10 10"><circle cx="5" cy="5" r="4" fill="none" stroke="#333"/><path d="M5 2.5V5l2 1" stroke="#333" fill="none"/></svg>EVENT DURATION : <b>2:00 HRS</b></div>
  <div class="header-rule" style="right:145px"></div>
  <aside class="sidebar">
    <ul class="nav">
      <li>EVENT INFO</li>
      <li class="is-active">STAGE <svg width="6" height="6" viewBox="0 0 10 10"><path d="M5 1 9 3v4L5 9 1 7V3z" fill="#fff"/></svg></li>
      <li>BREAKOUTS</li><li>BOOTHS</li><li>VIRTUAL EXHIBITION</li><li>REWARDS</li>
    </ul>
    <div class="copyright">© 2020 www.venueloop.com</div>
  </aside>

  <h2 class="section-title" style="left:117px;top:50px">VIDEO</h2>
  <div class="photo" role="img" aria-label="Smiling woman in a striped shirt, video thumbnail" style="left:117px;top:77.5px;width:310px;height:137px;background:linear-gradient(90deg,#e8ecef 0%,#b9a99c 35%,#dfe1e6 60%,#e3e5ea 100%)"></div>
  <div class="frame" style="left:117px;top:77.5px;width:310px;height:137px"></div>
  <div class="corner-tr" style="left:409px;top:76px;height:18px"></div>
  <div class="corner-bl" style="left:115.5px;top:198px"></div>
  <div class="abs" style="left:288.6px;top:131px;font-size:9.5px;font-weight:600">The Biggest Conference</div>
  <div class="play" style="left:288.6px;top:145px"></div>
  <div class="abs" style="left:312px;top:151px;font-size:5px;font-weight:600;color:var(--heading)">Watch the video</div>

  <h2 class="section-title" style="left:113.5px;top:236px">PROGRAMMING</h2>
  <div class="session" style="left:113.5px"><div class="photo" role="img" aria-label="Presenter speaking to a seated audience"></div><small>Duration : 1:56 hrs</small><strong>Lorem ipsum dolor sit amet</strong></div>
  <div class="session" style="left:219px"><div class="photo" role="img" aria-label="Speaker holding a microphone"></div><small>Duration : 1:56 hrs</small><strong>Lorem ipsum dolor sit amet</strong></div>
  <div class="session" style="left:324.6px"><div class="photo" role="img" aria-label="Speaker with a headset gesturing on stage"></div><small>Duration : 1:56 hrs</small><strong>Lorem ipsum dolor sit amet</strong></div>

  <aside class="chat">
    <div class="chat-head">Online Chat <em>VL</em></div>
    <div class="chat-item" style="top:26px"><i class="avatar" role="img" aria-label="Portrait of Daicy"></i><b>Daicy</b><span>The Speaker</span><span class="status">Online</span></div>
    <div class="chat-item" style="top:71px"><i class="avatar" role="img" aria-label="Portrait of Merry"></i><b style="top:13px">Merry</b><span style="top:24px">The Speaker</span></div>
    <div class="chat-item" style="top:116px"><i class="avatar" role="img" aria-label="Portrait of Jhon"></i><b style="top:13px">Jhon</b><span style="top:24px">The Speaker</span></div>
    <div class="chat-item" style="top:162px"><i class="avatar" role="img" aria-label="Portrait of James"></i><b style="top:13px">James</b><span style="top:24px">The Speaker</span></div>
    <div class="chat-item" style="top:210px"><i class="avatar" role="img" aria-label="Portrait of Droid"></i><b style="top:13px">Droid</b><span style="top:24px">The Speaker</span></div>
    <div class="chat-item" style="top:255px"><i class="avatar" role="img" aria-label="Portrait of David"></i><b style="top:13px">David</b><span style="top:24px">The Speaker</span></div>
    <div class="chat-item" style="top:304px;border:0"><i class="avatar" role="img" aria-label="Portrait of Linda"></i><b style="top:13px">Linda</b><span style="top:24px">The Speaker</span></div>
  </aside>
</section>

<!-- Breakouts screen -->
<section class="screen screen--breakouts">
  <div class="brand" style="left:15px">VENUELOOP</div>
  <div class="search" style="left:108px">Search
    <svg width="6" height="6" viewBox="0 0 10 10"><circle cx="4" cy="4" r="3" fill="none" stroke="#333"/><path d="M6.3 6.3 9 9" stroke="#333"/></svg></div>
  <div class="duration"><svg width="8" height="8" viewBox="0 0 10 10"><circle cx="5" cy="5" r="4" fill="none" stroke="#333"/><path d="M5 2.5V5l2 1" stroke="#333" fill="none"/></svg>EVENT DURATION : <b>2:00 HRS</b></div>
  <div class="header-rule"></div>
  <aside class="sidebar">
    <ul class="nav">
      <li>EVENT INFO</li><li>STAGE</li>
      <li class="is-active">BREAKOUTS <svg width="6" height="6" viewBox="0 0 10 10"><path d="M5 1 9 3 5 5 1 3z M1 5l4 2 4-2 M1 7l4 2 4-2" fill="#fff" stroke="#fff" stroke-width=".8"/></svg></li>
      <li>BOOTHS</li><li>VIRTUAL EXHIBITION</li><li>REWARDS</li>
    </ul>
    <div class="copyright">© 2020 www.venueloop.com</div>
  </aside>

  <div class="room room--dark" style="left:112px;top:60.7px"><h4>JOIN BREAKOUT ROOM 1</h4><span class="count">4/50</span><span class="time">3.00pm to 4.30pm</span><a>(Link to 3rd Party MEETSPACE Room)</a></div>
  <div class="room room--light" style="left:263px;top:60.7px"><h4>JOIN BREAKOUT ROOM 1</h4><span class="count">10/50</span><span class="time">3.00pm to 4.30pm</span><a>(Link to 3rd Party MEETSPACE Room)</a></div>
  <div class="room room--dark" style="left:414px;top:60.7px"><h4>JOIN BREAKOUT ROOM 1</h4><span class="count">20/50</span><span class="time">3.00pm to 4.30pm</span><a>(Link to 3rd Party MEETSPACE Room)</a></div>
  <div class="room room--light" style="left:112px;top:139px"><h4>JOIN BREAKOUT ROOM 1</h4><span class="count">4/50</span><span class="time">3.00pm to 4.30pm</span><a>(Link to 3rd Party MEETSPACE Room)</a></div>
  <div class="room room--dark" style="left:263px;top:139px"><h4>JOIN BREAKOUT ROOM 1</h4><span class="count">9/50</span><span class="time">3.00pm to 4.30pm</span><a>(Link to 3rd Party MEETSPACE Room)</a></div>
  <div class="room room--light" style="left:414px;top:139px"><h4>JOIN BREAKOUT ROOM 1</h4><span class="count">15/50</span><span class="time">3.00pm to 4.30pm</span><a>(Link to 3rd Party MEETSPACE Room)</a></div>
</section>

</body>
</html>
```